Online interactive tutorial for year 2 to year 12 students in Australia

Website design for a new online tutorial for year 2 to year 12 students in Australia.

- The tutorial will be conducted via live webcam and within a dedicated interactive space
- The tutorial will be provided by high scoring undergraduates studying in top Australian universities.
- The tutors will be going through interviews & assessments & only top students are allowed to apply.
- Parents will do search and select tutor and have short 15 mins video interaction with potential tutors before booking them for their children for tutoring.
- hourly cost of booking (no monthly subscription or no hour limits)
- Tutors will have their own profile

Please see the attached for detailed page functionality.

The look and feel of the design must consider the following:
- must be educational but not dull and should stand out
- must appeal to younger generation - tutees (8-18 years), tutors (19-25), parents (30-50).
- Ideas for Logos (brivora.com.au but not confirmed)

Target Market(s)

tutees (8-18 years), tutors (19-25 years), parents (30-50 years).

Industry/Entity Type

Education

Coding

Coded - Design and coding required

Number of Pages Required

5+ page

Font styles to use
Serif

Requirements
Must have
• The look and feel of the design must consider the following:
• - must be educational but not dull and should stand out
• - must appeal to younger generation - tutees (8-18 years), tutors (19-25), parents (30-50).
Should not have
• Dullness

```html
<!DOCTYPE html>
<html lang="en">
<head>
<meta charset="utf-8">
<title>Brivora – Learning Space</title>
<link href="https://fonts.googleapis.com/css2?family=Open+Sans:wght@400;600;700&family=Roboto+Condensed:wght@400;700&display=swap" rel="stylesheet">
<style>
:root{
  --blue:#2b86d1;
  --blue-dark:#1f6fb4;
  --text:#444;
  --muted:#666;
  --border:#cfcfcf;
  --footer:#333;
  --red:#e02424;
  --yellow:#f8c13d;
  --teal:#25c3b0;
  --coral:#f25a5f;
  --green:#3bb43a;
  --cyan:#1fc6c0;
  --sky:#1c9ee6;
  --crimson:#e3262a;
}
*{box-sizing:border-box;margin:0;padding:0}
html,body{width:895px;height:1200px;overflow:hidden}
body{position:relative;font-family:"Open Sans",sans-serif;color:var(--text);background:#fff}
.abs{position:absolute}
.brand{left:73px;top:24px;display:flex;align-items:center;gap:8px;font:700 28px "Open Sans",sans-serif;color:#555}
.brand-dot{width:30px;height:30px;border-radius:50%;background:var(--blue)}
.search{left:270px;top:27px;width:269px;height:26px;border:1px solid var(--border);border-radius:3px;font-size:9px;color:#555;padding:7px 10px}
.search-btn{position:absolute;right:0;top:0;width:28px;height:24px;background:#eee;border-left:1px solid var(--border)}
.role{top:29px;height:24px;border:2px solid var(--blue);color:var(--blue);font-size:10px;display:flex;align-items:center;justify-content:center;gap:4px}
.login{left:770px;top:29px;width:51px;height:24px;background:var(--blue);color:#fff;font-size:10px;display:flex;align-items:center;justify-content:center;border-radius:2px}
.nav{left:0;top:86px;width:895px;height:37px;background:var(--blue);display:flex;padding-left:73px}
.nav a{color:#fff;text-decoration:none;font:400 10px "Roboto Condensed",sans-serif;padding:0 18px;line-height:37px;border-right:1px solid rgba(255,255,255,.25)}
.nav a:last-child{border-right:none}
.hero{left:0;top:123px;width:895px;height:240px;background:linear-gradient(110deg,#8f8a84 0%,#c9bfb1 45%,#b5ab9d 70%,#6f7d5a 100%)}
.hero-title{left:0;top:233px;width:895px;text-align:center;font:700 32px "Roboto Condensed",sans-serif;color:#fff;text-shadow:0 2px 4px rgba(0,0,0,.35)}
.avatar{left:368px;top:294px;width:158px;height:158px;border-radius:50%;border:3px solid var(--blue);background:linear-gradient(160deg,#c9a07a,#e9d2bd 55%,#8a5f45)}
.cam{left:431px;top:432px;width:32px;height:32px;border-radius:50%;background:var(--blue);border:2px solid #fff;display:flex;align-items:center;justify-content:center}
.timer{left:107px;top:398px;width:158px;height:38px;border:1px solid var(--border);text-align:center;font:700 10.5px/15px "Open Sans",sans-serif;color:#444;padding-top:4px}
.side-btn{left:676px;width:113px;border:1px solid var(--border);font-size:10px;line-height:11px;color:#555;display:flex;align-items:center;gap:7px;padding-left:12px}
.tool{top:502px;width:100px;text-align:center}
.tool .disc{width:62px;height:62px;border-radius:50%;margin:0 auto;display:flex;align-items:center;justify-content:center}
.tool span{display:block;margin-top:10px;font-size:11.5px;color:#555}
.panel{left:107px;top:626px;width:682px;height:228px;border:1px solid #ddd;background:#f7f7f7}
.tabs{display:flex;height:56px;padding-left:14px}
.tab{text-align:center;font-size:10.5px;color:#555;padding:9px 20px 0;border-right:1px solid #e4e4e4}
.tab:last-child{border-right:none}
.tab svg{display:block;margin:0 auto 4px}
.editor{position:absolute;left:17px;top:56px;width:647px;height:152px;background:#fff;border:1px solid #e6e6e6;font-size:9px;color:#444;padding:22px 14px}
.act{top:877px;width:73px;height:24px;color:#fff;font-size:11px;display:flex;align-items:center;justify-content:center;border-radius:2px}
.footer{left:0;top:946px;width:895px;height:217px;background:var(--footer);color:#fff}
.fh{position:absolute;top:28px;font:400 13px "Roboto Condensed",sans-serif;letter-spacing:.2px}
.ft{position:absolute;font-size:9.5px;line-height:15px}
.links{position:absolute;left:316px;top:60px;list-style:none;font-size:9.5px;line-height:16px}
.links li::before{content:"";display:inline-block;border-left:4px solid #fff;border-top:3px solid transparent;border-bottom:3px solid transparent;margin-right:10px}
.social{position:absolute;left:750px;top:60px;list-style:none;font-size:11px}
.social li{display:flex;align-items:center;gap:8px;height:27px}
.social i{width:19px;height:19px;border:1px solid #fff;border-radius:50%;display:inline-block}
.name-in{position:absolute;left:465px;top:93px;width:219px;height:30px;background:#fff;color:#555;font-size:8.5px;padding:10px 10px}
.subscribe{position:absolute;left:465px;top:131px;width:76px;height:31px;background:#1c9ee6;font-size:10px;display:flex;align-items:center;justify-content:center}
.bottom{left:0;top:1163px;width:895px;height:37px;background:var(--blue);color:#fff;font-size:9px;text-align:center;line-height:37px}
</style>
</head>
<body>

<header>
  <div class="abs brand"><span class="brand-dot"></span>Brivora</div>
  <div class="abs search">Search
    <div class="search-btn"><svg width="28" height="24"><circle cx="13" cy="11" r="4" fill="none" stroke="#444" stroke-width="1.6"/><line x1="16" y1="14" x2="19" y2="17" stroke="#444" stroke-width="1.6"/></svg></div>
  </div>
  <div class="abs role" style="left:556px;width:57px">Tutor</div>
  <div class="abs role" style="left:622px;width:61px">Parent</div>
  <div class="abs role" style="left:692px;width:69px">Tutees</div>
  <div class="abs login">LOGIN</div>
</header>

<nav class="abs nav">
  <a>HOME</a><a>TUTOR PROFILES</a><a>HOW IT WORKS</a><a>TESTIMONIALS</a><a>PRICES</a><a>CONTACT US</a>
</nav>

<section>
  <div class="abs hero" role="img" aria-label="Desk photo with keyboard, notebook, pencil and plant"></div>
  <svg class="abs" style="left:0;top:300px" width="895" height="70">
    <polygon points="0,15 447,55 895,15 895,70 0,70" fill="#fff"/>
    <polyline points="0,15 447,55 895,15" fill="none" stroke="var(--blue)" stroke-width="3"/>
  </svg>
  <h1 class="abs hero-title">LEARNING SPACE</h1>
  <div class="abs avatar" role="img" aria-label="Portrait photo of the tutor"></div>
  <div class="abs cam"><svg width="16" height="16"><circle cx="8" cy="8" r="6" fill="#fff"/><circle cx="8" cy="8" r="3" fill="#333"/></svg></div>

  <div class="abs timer">Session Time Remaining :<br>56m &nbsp;45s</div>
  <div class="abs side-btn" style="top:373px;height:26px">
    <svg width="10" height="10"><path d="M5 0v6M2 3l3 3 3-3M0 9h10" stroke="#555" fill="none" stroke-width="1.5"/></svg>Uploaded Work</div>
  <div class="abs side-btn" style="top:404px;height:32px">
    <svg width="10" height="10"><rect x="0.5" y="0.5" width="9" height="9" fill="none" stroke="#555"/><rect x="2.5" y="0.5" width="5" height="3" fill="#555"/></svg>Work Saved In<br>Past Sessions</div>
  <div class="abs side-btn" style="top:441px;height:32px">
    <svg width="10" height="10"><rect x="0.5" y="0.5" width="9" height="9" fill="none" stroke="#555"/><rect x="2.5" y="0.5" width="5" height="3" fill="#555"/></svg>Saved Past<br>Sessions</div>
</section>

<section>
  <div class="abs tool" style="left:95px"><div class="disc" style="background:var(--yellow)"><svg width="28" height="26"><rect x="2" y="4" width="20" height="20" fill="none" stroke="#fff" stroke-width="2.5"/><path d="M6 11h10M6 16h10M6 20h7" stroke="#fff" stroke-width="2"/><path d="M26 2l-9 11" stroke="#fff" stroke-width="3"/></svg></div><span>Writing Pad</span></div>
  <div class="abs tool" style="left:193px"><div class="disc" style="background:var(--teal)"><svg width="30" height="26"><rect x="2" y="6" width="26" height="18" fill="none" stroke="#fff" stroke-width="2.5"/><path d="M24 2l-10 12" stroke="#fff" stroke-width="3"/></svg></div><span>Drawing Pad</span></div>
  <div class="abs tool" style="left:291px"><div class="disc" style="background:var(--coral)"><svg width="26" height="26"><rect x="2" y="2" width="22" height="22" rx="2" fill="none" stroke="#fff" stroke-width="2.5"/><rect x="7" y="2" width="12" height="7" fill="none" stroke="#fff" stroke-width="2"/><rect x="7" y="14" width="12" height="8" fill="#fff"/></svg></div><span>Save Work</span></div>
  <div class="abs tool" style="left:390px"><div class="disc" style="background:var(--green)"><svg width="30" height="28"><path d="M15 2l-8 9h5v8h6v-8h5z" fill="#fff"/><rect x="2" y="20" width="26" height="7" rx="1" fill="#fff"/></svg></div><span>Upload Work</span></div>
  <div class="abs tool" style="left:494px"><div class="disc" style="background:var(--cyan)"><svg width="24" height="28"><path d="M2 2h14l6 6v18H2z" fill="none" stroke="#fff" stroke-width="2.5"/><path d="M6 12h12M6 17h12M6 22h8" stroke="#fff" stroke-width="2"/></svg></div><span>Access to Docs</span></div>
  <div class="abs tool" style="left:591px"><div class="disc" style="background:var(--sky)"><svg width="28" height="26"><rect x="2" y="2" width="24" height="22" fill="none" stroke="#fff" stroke-width="2.5"/><path d="M2 9h24M2 16h24M11 2v22M19 2v22" stroke="#fff" stroke-width="1.6"/></svg></div><span>Sheets</span></div>
  <div class="abs tool" style="left:691px"><div class="disc" style="background:var(--crimson)"><svg width="30" height="28"><path d="M5 2h14l6 6v18H5z" fill="none" stroke="#fff" stroke-width="2.5"/><text x="15" y="21" font-size="8" font-weight="700" fill="#fff" text-anchor="middle" font-family="Open Sans,sans-serif">PDF</text></svg></div><span>Pdf Application</span></div>
</section>

<section class="abs panel">
  <div class="tabs">
    <div class="tab"><svg width="14" height="14"><path d="M2 12l1-4 7-7 3 3-7 7z" fill="#555"/></svg>Post Comments</div>
    <div class="tab"><svg width="14" height="14"><circle cx="10" cy="3" r="2.5" fill="#555"/><circle cx="3" cy="7" r="2.5" fill="#555"/><circle cx="10" cy="11" r="2.5" fill="#555"/><path d="M10 3L3 7l7 4" stroke="#555" fill="none"/></svg>Share</div>
    <div class="tab"><svg width="14" height="14"><path d="M7 1l-4 4h3v4h2V5h3z" fill="#555"/><rect x="1" y="10" width="12" height="3" fill="#555"/></svg>Upload</div>
    <div class="tab"><svg width="16" height="14"><path d="M1 3h5l1 2h7v7H1z" fill="#555"/></svg>Open</div>
    <div class="tab"><svg width="14" height="14"><rect x="1" y="1" width="12" height="12" fill="none" stroke="#555" stroke-width="1.5"/><rect x="4" y="1" width="6" height="4" fill="#555"/></svg>saved</div>
  </div>
  <div class="editor">Sed ut perspiciatis unde omnis iste natus|</div>
</section>

<div class="abs act" style="left:370px;background:var(--red)">Recorded</div>
<div class="abs act" style="left:453px;background:var(--blue)">Saved</div>

<footer class="abs footer">
  <h3 class="fh" style="left:73px">CONTACT US</h3>
  <p class="ft" style="left:73px;top:61px">Level 3, 22 Harbour Lane, Brisbane<br>QLD 4000, Australia</p>
  <svg class="abs" style="left:75px;top:98px" width="14" height="14"><path d="M2 1l3 0 1 4-2 1a8 8 0 0 0 4 4l1-2 4 1 0 3c-6 1-12-5-11-11z" fill="none" stroke="#fff"/></svg>
  <p class="ft" style="left:101px;top:96px">Phone : +61 7 3000 1482<br>Fax : +61 7 3000 1483</p>
  <svg class="abs" style="left:75px;top:137px" width="15" height="11"><rect x="0.5" y="0.5" width="14" height="10" fill="none" stroke="#fff"/><path d="M0.5 0.5l7 5 7-5" fill="none" stroke="#fff"/></svg>
  <p class="ft" style="left:101px;top:134px">Email: info@brivora.com.au</p>

  <h3 class="fh" style="left:316px">USEFUL LINKS</h3>
  <ul class="links"><li>Home</li><li>About Us</li><li>Services</li><li>Tutor Profile</li><li>How It Works</li><li>Scheduler</li><li>Testimonials</li><li>Contact Us</li></ul>

  <h3 class="fh" style="left:465px">JOIN OUR NEWSLETTER</h3>
  <p class="ft" style="left:465px;top:59px;font-size:8.5px;line-height:14px;width:230px">Sed ut perspiciatis unde omnis iste natus error sit volup-<br>tatem accusantium doloremque laudantium,</p>
  <div class="name-in">Enter Name</div>
  <div class="subscribe">SUBSCRIBE</div>

  <h3 class="fh" style="left:750px">SOCIAL</h3>
  <ul class="social"><li><i></i>Pagefeed</li><li><i></i>Chirper</li><li><i></i>Circlenet</li><li><i></i>Vidstream</li></ul>
</footer>

<div class="abs bottom">Copyright 2016 | All Rights Reserved -- Brivora</div>

</body>
</html>
```